R7M Horizon Business Card Design

We need a business card created for our New Business "R7M Horizon"<br/><br/>The business card design is up to you however the following information must be on the business card:<br/><br/>Front of the business card -<br/>Email :darrenp@r7mhorizon.nz<br/>Mobile: +64 (0) 22 4870 619<br/>Website: www.r7mhorizon.nz<br/>Card Owner Name: Darren Paltrow<br/>Company Title: Business Development Manager<br/>Slogan: "The BEST of both worlds". <br/>Logo On the front attached to the design brief<br/><br/>On the back: <br/>Space on the back for 4 more versions of the logo across the bottom of the card indicating different subsidiary brands - R7M Coffee, R7M Arts, R7M ?? (The card will be used for all of these brands - We Will add the extra subsidiary logos to the design once the design is finished (We are a graphics design team). <br/><br/>Other than that we want a premium feeling logo that remains universally usable depending on the business entity that we are using the card for. The use of bright bold colours would be great but we still want the card to feel premium.
Target Market(s)
Gift Design and Manufacturing Companies
Contact Information for Business Card
Front of the business card -
Email :darrenp@r7mhorizon.nz
Mobile: +64 (0) 22 4870 619
Website: www.r7mhorizon.nz
Card Owner Name: Darren Paltrow
Company Title: Business Development Manager
Slogan: "The BEST of both worlds".
Logo On the front attached to the design brief

```html
<!DOCTYPE html>
<html lang="en">
<head>
<meta charset="utf-8">
<title>R7M Horizon Business Card</title>
<link href="https://fonts.googleapis.com/css2?family=Open+Sans:ital,wght@0,400;0,700;1,400;1,700&display=swap" rel="stylesheet">
<style>
  :root {
    --stage: #2b2b2d;
    --card: #1c1c1d;
    --ink: #f2f2f2;
    --accent: #3a4bc0;
    --emboss: #2e2e30;
  }
  * { margin: 0; padding: 0; box-sizing: border-box; }
  html, body { width: 1200px; height: 900px; overflow: hidden; }
  body {
    background: var(--stage);
    font-family: "Open Sans", Arial, sans-serif;
    display: flex;
    flex-direction: column;
    align-items: center;
    justify-content: center;
    gap: 40px;
  }
  .card {
    width: 700px;
    height: 400px;
    background: var(--card);
    position: relative;
    box-shadow: 0 14px 30px rgba(0,0,0,.45);
  }
  /* Back */
  .card--back { display: flex; align-items: center; justify-content: center; }
  .brand-name {
    font-size: 54px; font-weight: 700; color: var(--emboss);
    letter-spacing: 3px; text-transform: uppercase; white-space: nowrap;
  }
  /* Front */
  .identity {
    position: absolute; right: 372px; top: 118px; text-align: right;
  }
  .identity__name {
    color: var(--accent); font-weight: 700; font-style: italic;
    font-size: 27px; line-height: 36px; text-transform: uppercase; letter-spacing: .5px;
  }
  .identity__title { color: var(--ink); font-size: 19px; line-height: 28px; margin-top: 2px; white-space: nowrap; }
  .divider {
    position: absolute; left: 350px; top: 120px; width: 2px; height: 90px;
    background: var(--accent);
  }
  .contacts {
    position: absolute; left: 372px; top: 118px; list-style: none;
    color: var(--ink); font-size: 19px; line-height: 30px;
  }
  .contacts li { display: flex; align-items: center; gap: 10px; white-space: nowrap; }
  .contacts svg { width: 16px; height: 16px; fill: var(--accent); flex: none; }
  .slogan {
    position: absolute; left: 90px; top: 285px; color: var(--ink); font-size: 20px; white-space: nowrap;
  }
  .slogan strong { font-weight: 700; }
</style>
</head>
<body>
  <section class="card card--back" aria-label="Card back">
    <span class="brand-name">R7M Horizon</span>
  </section>

  <section class="card card--front" aria-label="Card front">
    <div class="identity">
      <h1 class="identity__name">Darren Paltrow</h1>
      <p class="identity__title">Business Development Manager</p>
    </div>
    <span class="divider"></span>
    <ul class="contacts">
      <li>
        <svg viewBox="0 0 16 16"><path d="M4 0h8a1 1 0 0 1 1 1v14a1 1 0 0 1-1 1H4a1 1 0 0 1-1-1V1a1 1 0 0 1 1-1zm.5 2v10h7V2zM8 13a1 1 0 1 0 0 2 1 1 0 0 0 0-2z"/></svg>
        +64 (0) 22 4870 619
      </li>
      <li>
        <svg viewBox="0 0 16 16"><path d="M0 3h16v1.2L8 9 0 4.2zM0 5.6l8 4.8 8-4.8V13H0z"/></svg>
        darrenp@r7mhorizon.nz
      </li>
      <li>
        <svg viewBox="0 0 16 16"><path d="M8 0a8 8 0 1 0 0 16A8 8 0 0 0 8 0zm5.9 7h-2.5a12 12 0 0 0-1-4.6A6 6 0 0 1 13.9 7zM8 2c.8 1 1.3 2.9 1.4 5H6.6C6.7 4.9 7.2 3 8 2zM5.6 2.4a12 12 0 0 0-1 4.6H2.1a6 6 0 0 1 3.5-4.6zM2.1 9h2.5a12 12 0 0 0 1 4.6A6 6 0 0 1 2.1 9zM8 14c-.8-1-1.3-2.9-1.4-5h2.8c-.1 2.1-.6 4-1.4 5zm2.4-.4a12 12 0 0 0 1-4.6h2.5a6 6 0 0 1-3.5 4.6z"/></svg>
        www.r7mhorizon.nz
      </li>
    </ul>
    <p class="slogan">The <strong>BEST</strong> of both worlds</p>
  </section>
</body>
</html>
```